New Business Card Design Project

Need a design that will create an impact / strong impression towards our clients for our business. We are in the lighting business and we do lighting retrofits for large commercial to industrial clientele.

Target Market(s)

Lighting Industry

Industry/Entity Type

Business

Font styles to use
Other font styles liked:
• we would like to use the font on our logo, not sure what it is though..

Requirements
Must have
• Our logo.
Nice to have
• We are open to suggestions that have to do with lighting.

```html
<!DOCTYPE html>
<html lang="en">
<head>
<meta charset="utf-8">
<title>Lumen Upgrade Partners – Business Cards</title>
<link rel="stylesheet" href="https://fonts.googleapis.com/css2?family=Open+Sans:wght@400;600;700&display=swap">
<style>
  :root {
    --bg: #e9e7e3;
    --card-white: #ffffff;
    --card-dark: #2b2b2b;
    --green-dark: #0d5a1f;
    --green: #1f8a2e;
    --green-light: #5cc14a;
    --ink: #1e1e1e;
    --paper-edge: #cfcfcf;
  }
  * { margin: 0; padding: 0; box-sizing: border-box; }
  html, body { width: 1200px; height: 900px; overflow: hidden; }
  body {
    background: var(--bg);
    font-family: "Open Sans", Arial, sans-serif;
    position: relative;
  }
  .card {
    position: absolute;
    width: 600px;
    height: 343px;
    border-radius: 4px;
    box-shadow: 0 3px 0 var(--paper-edge), 0 6px 0 #bdbdbd, 0 14px 26px rgba(0,0,0,.25);
    overflow: hidden;
  }
  .brand {
    display: flex; align-items: center; gap: 12px;
    font-weight: 700; letter-spacing: .5px; white-space: nowrap;
  }
  .brand-mark { width: 20px; height: 20px; flex: none; }

  /* back side */
  .card-back {
    left: 530px; top: 90px;
    background: var(--card-dark);
    display: flex; align-items: center; justify-content: center;
  }
  .card-back .brand { color: #ffffff; font-size: 30px; }
  .card-back .brand-mark { background: #ffffff; width: 22px; height: 22px; }

  /* front side */
  .card-front {
    left: 70px; top: 440px;
    background: var(--card-white);
  }
  .corner-tab { position: absolute; left: 0; top: 22px; }
  .person { position: absolute; left: 70px; top: 24px; }
  .person-name { color: var(--green); font-weight: 700; font-size: 25px; line-height: 1.1; }
  .person-role { color: var(--ink); font-size: 15px; }
  .contact {
    position: absolute; left: 28px; top: 130px;
    list-style: none; color: var(--ink); font-size: 16px; line-height: 1.45;
  }
  .contact li { display: flex; align-items: center; gap: 8px; }
  .contact .no-icon { padding-left: 22px; }
  .contact svg { width: 14px; height: 14px; fill: var(--green); flex: none; }
  .card-front .brand {
    position: absolute; right: 34px; top: 168px;
    color: var(--green); font-size: 22px;
  }
  .card-front .brand-mark { background: var(--green); }
  .footer-band { position: absolute; left: 0; bottom: 0; display: block; }
</style>
</head>
<body>
  <section class="card card-back" aria-label="Card back">
    <div class="brand"><span class="brand-mark"></span>Lumen Upgrade Partners</div>
  </section>

  <section class="card card-front" aria-label="Card front">
    <svg class="corner-tab" width="60" height="44" viewBox="0 0 60 44">
      <polygon points="0,0 60,0 60,44 0,44" fill="var(--green-dark)"/>
      <polygon points="0,44 60,0 60,44" fill="var(--green)"/>
    </svg>
    <div class="person">
      <p class="person-name">Daniel Reyes</p>
      <p class="person-role">Managing Director</p>
    </div>
    <ul class="contact">
      <li class="no-icon">48 Harbor Lane, Suite 210</li>
      <li class="no-icon">Brookfield, 560204.</li>
      <li><svg viewBox="0 0 24 24"><path d="M6.6 10.8a15 15 0 0 0 6.6 6.6l2.2-2.2c.3-.3.7-.4 1-.2 1.1.4 2.3.6 3.6.6.6 0 1 .4 1 1V20c0 .6-.4 1-1 1A17 17 0 0 1 3 4c0-.6.4-1 1-1h3.5c.6 0 1 .4 1 1 0 1.3.2 2.5.6 3.6.1.3 0 .7-.2 1z"/></svg>044-555 018 274</li>
      <li><svg viewBox="0 0 24 24"><path d="M2 5h20v14H2z M2 5l10 8 10-8" stroke="#fff" stroke-width="1.5"/></svg>hello@lumenupgrade.com</li>
      <li><svg viewBox="0 0 24 24"><path d="M10 14a4 4 0 0 0 5.7 0l4-4a4 4 0 0 0-5.7-5.7l-1.5 1.5 1.4 1.4 1.5-1.5a2 2 0 1 1 2.9 2.9l-4 4a2 2 0 0 1-2.9 0zM14 10a4 4 0 0 0-5.7 0l-4 4a4 4 0 0 0 5.7 5.7l1.5-1.5-1.4-1.4-1.5 1.5a2 2 0 1 1-2.9-2.9l4-4a2 2 0 0 1 2.9 0z"/></svg>www.lumenupgrade.com</li>
    </ul>
    <div class="brand"><span class="brand-mark"></span>Lumen Upgrade Partners</div>
    <svg class="footer-band" width="600" height="44" viewBox="0 0 600 44">
      <defs>
        <linearGradient id="bandShade" x1="0" y1="0" x2="0" y2="1">
          <stop offset="0" stop-color="var(--green)"/>
          <stop offset="1" stop-color="var(--green-light)"/>
        </linearGradient>
      </defs>
      <rect x="0" y="0" width="600" height="44" fill="url(#bandShade)"/>
      <polygon points="212,0 222,0 204,16 194,16" fill="#ffffff"/>
    </svg>
  </section>
</body>
</html>
```